Wordpress theme website for professionals working together

My partner and I are offering business services, my wife in the energy business as mainly as member of the board of commissioners. I am working as interim manager/consultant in the accounting and finance area. Both activities are connected in one company VELMOT BV (dutch ltd). We need a CV based website. Beside this we do some financial and accounting services.

Target Market(s)

small medium business

Font styles to use
Sans Serif

Colors

Designer to choose colors to be used in the design.

Requirements
Must have
• Pictures of both members.
• CLEAN AND SIMPLE
• I LIKE BLACK & WHITE
Nice to have
• I like design like this theme: http://theme.pruxelo-example.com/resume/

```html
<!DOCTYPE html>
<html lang="en">
<head>
<meta charset="utf-8">
<title>VELMOT BV</title>
<link rel="stylesheet" href="https://fonts.googleapis.com/css2?family=Lato:wght@400;700;900&display=swap">
<style>
:root{
  --ink:#111111;
  --text:#333333;
  --muted:#555555;
  --white:#ffffff;
  --hero-bg:#cfd3dc;
  --dark-band:#222222;
  --light-band:#f1f1f1;
  --bar-track:#e6e6e6;
  --bar-fill:#2a2a2a;
  --field-border:#bdbdbd;
  --social:#444444;
}
*{box-sizing:border-box;margin:0;padding:0}
html,body{width:1200px;height:2946px;overflow:hidden}
body{font-family:'Lato',sans-serif;color:var(--text);background:var(--white);position:relative}
section,header,footer{position:absolute;left:0;width:1200px}
.section-title{position:absolute;left:0;width:100%;text-align:center;font-weight:900;font-size:31px;color:var(--ink);letter-spacing:.5px}

/* header */
.site-header{top:0;height:105px;background:var(--white)}
.brand{position:absolute;left:76px;top:36px;font-size:45px;font-weight:900;color:var(--ink);letter-spacing:.5px}
.main-nav{position:absolute;right:52px;top:56px;display:flex;gap:34px;font-size:13px;text-transform:uppercase;color:var(--ink)}
.main-nav .active{font-weight:700}

/* hero */
.hero{top:105px;height:492px;background:var(--hero-bg);overflow:hidden}
.hero-photo{position:absolute;right:0;top:0;width:660px;height:492px;background:linear-gradient(90deg,var(--hero-bg) 0%,#b9b3ae 35%,#8d837c 60%,#5f5e66 100%)}
.person-name{position:absolute;left:72px;top:52px;font-size:46px;font-weight:700;color:var(--ink)}
.jobs-label{position:absolute;left:76px;top:126px;font-size:17px;font-weight:700;color:var(--ink)}
.job{position:absolute;left:76px;width:570px}
.job h3{font-size:20px;font-weight:700;color:var(--ink);margin-bottom:10px}
.job p{font-size:16.5px;line-height:23px;color:var(--text)}
.partner-card{position:absolute;left:75px;top:355px;display:flex;align-items:center}
.partner-avatar{width:97px;height:97px;border-radius:50%;background:radial-gradient(circle at 50% 45%,#8a6f62 0%,#3b2e2a 60%,#1e2a4a 100%)}
.partner-info{margin-left:25px}
.partner-info h4{font-size:19px;font-weight:700;color:var(--ink);margin-bottom:12px}
.btn-light{display:block;width:117px;height:40px;background:var(--white);color:var(--ink);font-size:15px;text-align:center;line-height:40px}

/* skills */
.skills{top:597px;height:531px}
.skills .section-title{top:58px}
.skill-list{position:absolute;left:0;top:142px;width:100%}
.skill{position:absolute;left:0;width:100%;height:20px;font-size:15px;color:var(--ink)}
.skill-label{position:absolute;right:705px;top:0;text-align:right;white-space:nowrap}
.skill-bar{position:absolute;left:525px;top:4px;width:359px;height:14px;background:var(--bar-track)}
.skill-bar span{display:block;height:100%;background:var(--bar-fill)}
.skill-value{position:absolute;left:932px;top:0}

/* finished jobs */
.finished{top:1128px;height:282px;background:var(--dark-band);color:var(--white)}
.finished .section-title{top:44px;color:var(--white)}
.column{position:absolute;width:320px}
.column h3{font-size:20px;font-weight:700;margin-bottom:12px}
.column p{font-size:15px;line-height:23px}
.finished .column{top:117px}
.finished .column p{color:#d8d8d8}

/* education */
.education{top:1410px;height:282px}
.education .section-title{top:58px}
.education .column{top:124px;text-align:center;width:310px}
.education .column h3{color:var(--ink)}
.education .column p{color:var(--text)}

/* worked for */
.worked-for{top:1692px;height:276px;background:var(--light-band)}
.worked-for .section-title{top:40px}
.clients{position:absolute;left:0;top:148px;width:100%;display:flex;justify-content:center;align-items:center;gap:70px}
.client{font-size:30px;font-weight:700;color:var(--ink);letter-spacing:1px}

/* other */
.other{top:1968px;height:397px}
.other .section-title{top:52px}
.hobby-photo{position:absolute;left:254px;top:120px;width:333px;height:210px;background:linear-gradient(120deg,#3a3022 0%,#8a6a3e 40%,#d9b36a 60%,#5a4a2c 100%)}
.hobby-text{position:absolute;left:614px;top:135px;width:325px}
.hobby-text h3{font-size:20px;font-weight:700;color:var(--ink);margin-bottom:10px}
.hobby-text p{font-size:15px;line-height:23px}

/* contact */
.contact{top:2365px;height:403px;background:var(--light-band)}
.contact .section-title{top:50px}
.contact-form{position:absolute;left:254px;top:114px;width:692px}
.field{position:absolute;background:var(--white);border:1px solid var(--field-border);font-size:13px;color:var(--ink);padding:12px 13px;font-family:inherit}
.field-name{left:0;top:0;width:333px;height:40px}
.field-email{left:360px;top:0;width:332px;height:40px}
.field-message{left:0;top:49px;width:692px;height:124px}
.btn-dark{position:absolute;left:243px;top:189px;width:207px;height:48px;background:var(--dark-band);color:var(--white);font-size:17px;font-weight:700;text-align:center;line-height:48px;border:0}

/* footer */
.site-footer{top:2768px;height:178px;background:var(--white)}
.footer-nav{position:absolute;left:0;top:47px;width:100%;display:flex;justify-content:center;gap:34px;font-size:13px;text-transform:uppercase;color:var(--ink)}
.copyright{position:absolute;left:0;top:86px;width:100%;text-align:center;font-size:12px;color:var(--muted)}
.social{position:absolute;left:0;top:118px;width:100%;display:flex;justify-content:center;gap:21px}
.social span{width:20px;height:20px;border-radius:50%;background:var(--social)}
</style>
</head>
<body>

<header class="site-header">
  <div class="brand">VELMOT BV</div>
  <nav class="main-nav">
    <span class="active">Home</span><span>Actual Jobs</span><span>Finished Jobs</span><span>Skills</span><span>Education</span><span>Contact</span><span>More...</span>
  </nav>
</header>

<section class="hero">
  <div class="hero-photo" role="img" aria-label="Portrait photo of Hendrik, smiling man with glasses"></div>
  <h1 class="person-name">Hendrik</h1>
  <div class="jobs-label">Actual Jobs:</div>
  <div class="job" style="top:152px">
    <h3>Advisor WLT</h3>
    <p>Lorem ipsum dolor sit amet, consectetur adipiscing elit. Donec ullamcorper, leo eu sollicitudin malesuada, nibh nunc condimentum lectus..</p>
  </div>
  <div class="job" style="top:246px">
    <h3>Advisor How &amp; knower</h3>
    <p>Lorem ipsum dolor sit amet, consectetur adipiscing elit. Donec ullamcorper, leo eu sollicitudin malesuada, nibh nunc condimentum lectus..</p>
  </div>
  <div class="partner-card">
    <div class="partner-avatar" role="img" aria-label="Portrait photo of partner Marieke"></div>
    <div class="partner-info">
      <h4>Marieke</h4>
      <span class="btn-light">Click Here</span>
    </div>
  </div>
</section>

<section class="skills">
  <h2 class="section-title">SKILLS</h2>
  <div class="skill-list">
    <div class="skill" style="top:0"><span class="skill-label">Annual reporting</span><div class="skill-bar"><span style="width:61%"></span></div><span class="skill-value">65%</span></div>
    <div class="skill" style="top:41.5px"><span class="skill-label">Financial monthly reporting</span><div class="skill-bar"><span style="width:42%"></span></div><span class="skill-value">40%</span></div>
    <div class="skill" style="top:83px"><span class="skill-label">Accounting</span><div class="skill-bar"><span style="width:96%"></span></div><span class="skill-value">98%</span></div>
    <div class="skill" style="top:124.5px"><span class="skill-label">Financial management</span><div class="skill-bar"><span style="width:76%"></span></div><span class="skill-value">88%</span></div>
    <div class="skill" style="top:166px"><span class="skill-label">Project management</span><div class="skill-bar"><span style="width:71%"></span></div><span class="skill-value">70%</span></div>
    <div class="skill" style="top:207.5px"><span class="skill-label">Team player</span><div class="skill-bar"><span style="width:100%"></span></div><span class="skill-value">100%</span></div>
    <div class="skill" style="top:249px"><span class="skill-label">Trouble shooter</span><div class="skill-bar"><span style="width:79%"></span></div><span class="skill-value">89%</span></div>
    <div class="skill" style="top:290.5px"><span class="skill-label">ETC.</span><div class="skill-bar"><span style="width:22%"></span></div><span class="skill-value">15%</span></div>
  </div>
</section>

<section class="finished">
  <h2 class="section-title">FINISHED JOBS</h2>
  <div class="column" style="left:75px"><h3>Controller a.i. WLT</h3><p>Nullam condimentum faucibus consequat. Aenean quis leo felis. Morbi hendrerit auctor purus, sed malesuada tortor...</p></div>
  <div class="column" style="left:433px"><h3>Advisor Delta Groen</h3><p>Nullam condimentum faucibus consequat. Aenean quis leo felis. Morbi hendrerit auctor purus, sed malesuada tortor...</p></div>
  <div class="column" style="left:795px"><h3>Financial director EKN</h3><p>Nullam condimentum faucibus consequat. Aenean quis leo felis. Morbi hendrerit auctor purus, sed malesuada tortor...</p></div>
</section>

<section class="education">
  <h2 class="section-title">EDUCATION</h2>
  <div class="column" style="left:266px"><h3>Verra (RA)</h3><p>Nullam condimentum faucibus consequat. Aenean quis leo felis. Morbi hendrerit auctor purus, sed malesuada tortor...</p></div>
  <div class="column" style="left:625px"><h3>Atheneum B</h3><p>Nullam condimentum faucibus consequat. Aenean quis leo felis. Morbi hendrerit auctor purus, sed malesuada tortor...</p></div>
</section>

<section class="worked-for">
  <h2 class="section-title">WORKED FOR</h2>
  <div class="clients">
    <div class="client">Traven</div>
    <div class="client">Klamer</div>
  </div>
</section>

<section class="other">
  <h2 class="section-title">OTHER</h2>
  <div class="hobby-photo" role="img" aria-label="Photo of a photographer holding a camera in a sunlit forest"></div>
  <div class="hobby-text">
    <h3>Fotography</h3>
    <p>Nullam condimentum faucibus consequat. Aenean quis leo felis. Morbi hendrerit auctor purus, sed malesuada tortor. Lorem ipsum dolor sit amet, consectetur adipiscing elit. Donec ullamcorper, leo eu sollicitudin malesuada, nibh nunc condimentum lectus..</p>
  </div>
</section>

<section class="contact">
  <h2 class="section-title">CONTACT US</h2>
  <div class="contact-form">
    <div class="field field-name">Name</div>
    <div class="field field-email">Email Address</div>
    <div class="field field-message">Message</div>
    <div class="btn-dark">SUBMIT</div>
  </div>
</section>

<footer class="site-footer">
  <nav class="footer-nav">
    <span>Home</span><span>Actual Jobs</span><span>Finished Jobs</span><span>Skills</span><span>Education</span><span>Contact</span><span>More...</span>
  </nav>
  <p class="copyright">Copyright© 2018 Company Name. All Right Reserved</p>
  <div class="social" aria-label="Social links">
    <span></span><span></span><span></span><span></span><span></span>
  </div>
</footer>

</body>
</html>
```